Strategy and Technology Consulting - Our Story and Values Page

Interior Page design – Our History and Our Values

Our homepage has been designed and we are looking for a design for one of the interior pages. This interior page tells the story of Our History and Our Values

Because the homepage has been designed, we would like this interior page to reflect the design of the homepage without being a mirror image of the homepage.

This site will be implemented in WordPress using the Elementor framework.

Font: Poppins medium and Poppins dark
Illustrations: Our homepage illustrations were designed by “Brelin 1974” on Quillmark. Compatible original or stock illustrations are welcome. Stock photography is also welcome. Brelin is also available through Brelin Tosamek on Ravolo

Uploaded Files
• Homepage design – this is the design we will use for our homepage. Contest entries should reflect this basic style but should be distinctly different from the homepage.
• Our History and Our Values – Wireframe – the basic layout of the page we are looking for.
• Our History and Our Values – Word document with the text supporting the wireframe.
• Color Palette – please use colors compatible with the palette attached.

Our Story - timeline
There is a timeline element in the wireframe. The wireframe displays this as a series of chevrons (arrows), but it does not need to be. Creativity in display of the timeline is appreciated.

Our Values
If you look at the Word document, you will see that there are a lot of words on the page. The winning design will present the information in a way that engages the user without overwhelming them with too much to read. For example, they may click on a value and see more information.

Target Market(s)

CIO's and Technology Executives

Number of Pages Required

1 page

Font styles to use
Sans Serif
Other font styles liked:
• Poppin

Requirements
Must have
• A timeline element, all of our values
Nice to have
• Clever timeline display

```html
<!DOCTYPE html>
<html lang="en">
<head>
<meta charset="utf-8">
<title>Northvale – Our Story and Values</title>
<link href="https://fonts.googleapis.com/css2?family=Poppins:wght@400;500;600;700;800&display=swap" rel="stylesheet">
<style>
:root{
  --navy:#1f4e79;
  --navy-dark:#16385a;
  --yellow:#f2b705;
  --ink:#1c1c1c;
  --text:#3d3d3d;
  --muted:#6b7280;
  --story-bg:#f2f3f5;
  --white:#ffffff;
  --footer:#3b4658;
  --footer-deep:#2c3545;
  --line:#d9dde3;
}
*{box-sizing:border-box;margin:0;padding:0}
html,body{width:1200px;height:3296px;overflow:hidden}
body{font-family:"Poppins",sans-serif;color:var(--text);background:var(--white);position:relative}
.abs{position:absolute}

/* Header */
.site-header{left:0;top:0;width:1200px;height:64px;background:var(--white);box-shadow:0 2px 10px rgba(0,0,0,.06);z-index:3}
.brand{left:112px;top:14px;display:flex;align-items:center;gap:8px;font-size:30px;font-weight:600;color:var(--navy);line-height:36px}
.brand-dot{width:14px;height:14px;border-radius:50%;background:var(--yellow)}
.main-nav{left:540px;top:22px;display:flex;gap:30px;font-size:13px;font-weight:500;color:var(--ink)}
.main-nav span::after{content:" ▾";font-size:9px;color:var(--muted)}
.main-nav span.plain::after{content:""}
.btn{background:var(--yellow);color:var(--white);font-weight:600;font-size:12px;border-radius:4px;text-align:center;letter-spacing:.5px}
.header-cta{left:980px;top:16px;width:120px;height:32px;line-height:32px}

/* Story */
.story{left:0;top:64px;width:1200px;height:540px;background:var(--story-bg)}
.section-title{font-size:38px;font-weight:700;color:var(--ink);letter-spacing:.5px}
.story-title{left:100px;top:148px}
.chevron{top:236px;width:300px;height:44px}
.chevron span{position:absolute;left:0;top:0;width:100%;line-height:44px;text-align:center;color:var(--white);font-weight:600;font-size:16px}
.stem{width:2px;height:96px;top:280px;background:#9aa3ad}
.milestones{top:372px;width:300px;background:var(--white);box-shadow:0 4px 14px rgba(0,0,0,.08);padding:22px 20px;height:184px}
.milestones li{list-style:none;font-size:13px;line-height:19px;color:var(--text);padding-left:18px;position:relative;margin-bottom:8px}
.milestones li::before{content:"";position:absolute;left:0;top:5px;width:8px;height:8px;background:var(--yellow)}

/* Values */
.values-title{left:100px;top:688px}
.value-card{left:100px;width:1000px;height:212px;background:var(--white);box-shadow:0 6px 22px rgba(0,0,0,.09);padding:34px 60px 0 248px}
.value-card h3{font-size:20px;font-weight:700;color:var(--ink);line-height:26px;margin-bottom:14px;text-transform:uppercase}
.value-card p{font-size:14px;line-height:24px;color:var(--text)}
.value-icon{position:absolute;left:140px;top:66px;width:80px;height:80px;border-radius:50%;display:flex;align-items:center;justify-content:center}
.icon-yellow{background:var(--yellow)}
.icon-blue{background:var(--navy)}
.value-icon svg{width:40px;height:40px;fill:none;stroke:var(--white);stroke-width:2.4;stroke-linecap:round;stroke-linejoin:round}
.value-rail{left:178px;top:760px;width:4px;height:1780px;border-left:3px dashed #e5e7ea}

/* Footer */
.footer-wave{left:0;top:2560px;width:1200px;height:736px}
.newsletter{left:132px;top:2596px;width:948px;height:200px;background:var(--yellow);border-radius:100px;padding:46px 0 0 84px}
.newsletter h2{font-size:34px;font-weight:700;color:var(--white);line-height:44px}
.newsletter p{font-size:13px;color:var(--white);line-height:19px;font-weight:500;width:340px;margin-top:6px}
.subscribe-field{left:566px;top:80px;width:310px;height:42px;background:var(--white);border-radius:21px;font-size:13px;color:var(--muted);line-height:42px;padding-left:44px}
.subscribe-field i{position:absolute;left:18px;top:15px;width:12px;height:12px;border-radius:50%;background:var(--yellow)}
.footer-brand{left:120px;top:2926px;display:flex;align-items:center;gap:8px;font-size:42px;font-weight:600;color:var(--white)}
.footer-brand .brand-dot{width:18px;height:18px}
.socials{left:160px;top:3008px;display:flex;gap:12px}
.socials i{display:block;width:30px;height:30px;border-radius:50%;background:var(--white)}
.footer-cta{left:164px;top:3064px;width:130px;height:32px;line-height:32px}
.footer-col h4{font-size:20px;font-weight:700;color:var(--white);margin-bottom:16px}
.footer-col li{list-style:none;font-size:12.5px;color:#e6e9ee;line-height:28px;padding-left:16px;position:relative}
.footer-col li::before{content:"›";position:absolute;left:0;color:var(--yellow);font-weight:700}
.contact-item{display:flex;gap:12px;margin-bottom:14px;font-size:12.5px;color:#e6e9ee;line-height:18px}
.contact-item b{display:block;width:18px;height:18px;border-radius:50%;background:var(--yellow);flex:none;margin-top:2px}
.contact-item strong{display:block;color:var(--yellow);font-weight:500}
.copyright{left:0;top:3248px;width:1200px;height:48px;background:var(--footer-deep);text-align:center;color:#e6e9ee;font-size:13px;line-height:48px}
.chat-bubble{left:1128px;top:3196px;width:40px;height:40px;border-radius:50%;background:var(--yellow)}
</style>
</head>
<body>

<header class="abs site-header">
  <div class="abs brand"><i class="brand-dot"></i>Northvale</div>
  <nav class="abs main-nav">
    <span class="plain">AI</span><span>ABOUT US</span><span>SERVICES</span><span>INSIGHTS</span><span>JOIN US</span>
  </nav>
  <div class="abs btn header-cta">CONTACT US</div>
</header>

<section class="abs story" aria-label="Our Story"></section>
<h2 class="abs section-title story-title">OUR STORY</h2>

<div class="abs chevron" style="left:120px">
  <svg width="300" height="44"><polygon points="0,0 280,0 300,22 280,44 0,44 16,22" fill="#1f4e79"/></svg>
  <span>2018 - 2019</span>
</div>
<div class="abs chevron" style="left:450px">
  <svg width="300" height="44"><polygon points="0,0 280,0 300,22 280,44 0,44 16,22" fill="#f2b705"/></svg>
  <span>2020 - 2021</span>
</div>
<div class="abs chevron" style="left:780px">
  <svg width="300" height="44"><polygon points="0,0 280,0 300,22 280,44 0,44 16,22" fill="#1f4e79"/></svg>
  <span>2022 AND ONWARD</span>
</div>

<div class="abs stem" style="left:150px"></div>
<div class="abs stem" style="left:480px"></div>
<div class="abs stem" style="left:810px"></div>

<ul class="abs milestones" style="left:120px">
  <li>Growth Strategy Focus</li>
  <li>Consistent, Modest Growth</li>
  <li>Preliminary Focus on Technology</li>
  <li>Evolve: implementing strategy is hard</li>
</ul>
<ul class="abs milestones" style="left:450px">
  <li>Pandemic Pauses Growth</li>
  <li>Rethinking</li>
  <li>the business model</li>
  <li>the delivery model</li>
</ul>
<ul class="abs milestones" style="left:780px">
  <li>Leadership Team for Focus on Essential Areas</li>
  <li>Rapid Growth</li>
  <li>Customer Success</li>
</ul>

<h2 class="abs section-title values-title">OUR VALUES</h2>
<div class="abs value-rail"></div>

<article class="abs value-card" style="top:784px">
  <div class="value-icon icon-yellow"><svg viewBox="0 0 40 40"><circle cx="20" cy="13" r="6"/><path d="M8 33c0-7 5-11 12-11s12 4 12 11"/></svg></div>
  <h3>The value of every human.<br>Regardless.</h3>
  <p>Each person's unique experiences and perspectives add vibrant hues to the tapestry of our shared existence. In a world where diversity paints the canvas of humanity, true beauty is found in recognizing the inherent and incalculable value of every human being.</p>
</article>

<article class="abs value-card" style="top:1036px">
  <div class="value-icon icon-blue"><svg viewBox="0 0 40 40"><circle cx="13" cy="15" r="5"/><circle cx="27" cy="15" r="5"/><path d="M4 31c0-5 4-8 9-8s9 3 9 8M18 31c0-5 4-8 9-8s9 3 9 8"/></svg></div>
  <h3>Collaboration</h3>
  <p>Collaboration in work transforms individual endeavors into symphonies of collective achievement. Through collaboration, diverse talents converge, fostering a rich exchange of ideas that amplifies creativity, accelerates progress, and brings forth solutions beyond what a single mind could conceive.</p>
</article>

<article class="abs value-card" style="top:1286px">
  <div class="value-icon icon-yellow"><svg viewBox="0 0 40 40"><path d="M20 6c2 6 9 9 9 17a9 9 0 0 1-18 0c0-5 3-7 4-10 2 3 3 4 5 4 0-4-1-7 0-11z"/></svg></div>
  <h3>Passion</h3>
  <p>Passion infuses our work with energy, transforming routine tasks into opportunities for creativity and innovation. Fueled by passion, individuals become unstoppable forces, driven to overcome challenges and achieve remarkable outcomes that benefit them and inspire those around them.</p>
</article>

<article class="abs value-card" style="top:1536px">
  <div class="value-icon icon-blue"><svg viewBox="0 0 40 40"><polygon points="20,5 24.5,15 35,16 27,23 29.5,34 20,28.5 10.5,34 13,23 5,16 15.5,15"/></svg></div>
  <h3>Excellence</h3>
  <p>Excellence isn't a destination; it's a continuous journey of refinement and growth. Striving for excellence cultivates a culture of continuous improvement, fostering innovation, credibility, and a lasting impact that resonates far beyond the immediate task.</p>
</article>

<article class="abs value-card" style="top:1786px">
  <div class="value-icon icon-yellow"><svg viewBox="0 0 40 40"><path d="M6 32l10-10 6 6 12-14"/><path d="M26 14h8v8"/></svg></div>
  <h3>Tenacity</h3>
  <p>Tenacity is the unwavering anchor that keeps us grounded amidst adversity, propelling us forward when faced with obstacles. The resilience to persist, adapt, and learn from setbacks leads to the mastery of skills and the fulfillment of ambitious goals.</p>
</article>

<article class="abs value-card" style="top:2036px">
  <div class="value-icon icon-blue"><svg viewBox="0 0 40 40"><path d="M14 24a9 9 0 1 1 12 0c-1.5 1.3-2 2.5-2 4h-8c0-1.5-.5-2.7-2-4z"/><path d="M16 32h8M17 36h6"/></svg></div>
  <h3>Solution Mindset</h3>
  <p>A solution mindset is the compass that directs our focus from problems to possibilities. It empowers us to navigate challenges with a proactive mindset, igniting a journey of exploration and innovation that not only resolves issues but also paves the way for continuous growth and success.</p>
</article>

<article class="abs value-card" style="top:2286px">
  <div class="value-icon icon-yellow"><svg viewBox="0 0 40 40"><path d="M20 33S6 25 6 15a7 7 0 0 1 14-2 7 7 0 0 1 14 2c0 10-14 18-14 18z"/></svg></div>
  <h3>Generosity</h3>
  <p>Generosity creates a virtuous cycle of goodwill, fostering a sense of unity and shared purpose among colleagues. By freely sharing knowledge, support, and resources, we uplift those around us and contribute to a collaborative environment where collective achievements flourish.</p>
</article>

<footer>
  <svg class="abs footer-wave" viewBox="0 0 1200 736" preserveAspectRatio="none">
    <path d="M0 110 C300 20 520 40 760 90 C960 130 1100 70 1200 30 L1200 736 L0 736 Z" fill="#3b4658"/>
  </svg>

  <div class="abs newsletter">
    <h2>Subscribe Our Newsletter</h2>
    <p>Subscribe our newsletter to receive the latest news and exclusive offers every week. No spam.</p>
    <div class="abs subscribe-field"><i></i>Enter email address</div>
  </div>

  <div class="abs footer-brand"><i class="brand-dot"></i>Northvale</div>
  <div class="abs socials"><i></i><i></i><i></i><i></i></div>
  <div class="abs btn footer-cta">CONTACT US</div>

  <div class="abs footer-col" style="left:496px;top:2908px">
    <h4>Quick links</h4>
    <ul><li>Home</li><li>About Us</li><li>Services</li><li>Insights</li><li>Join Us</li><li>Contact Us</li></ul>
  </div>
  <div class="abs footer-col" style="left:680px;top:2908px">
    <h4>Our Services</h4>
    <ul><li>Business Transformation</li><li>VIP Implementations</li><li>VIP Solutions</li><li>BI and Data</li><li>Building the Right Team</li><li>All Rights Reserved</li></ul>
  </div>
  <div class="abs footer-col" style="left:920px;top:2908px">
    <h4>Contact info</h4>
    <div class="contact-item"><b></b><div><strong>Email</strong>hello@northvale-example.com</div></div>
    <div class="contact-item"><b></b><div><strong>Phone</strong>+00 12 345 6789</div></div>
    <div class="contact-item"><b></b><div><strong>Location</strong>Some address line goes here<br>city name</div></div>
  </div>

  <div class="abs chat-bubble"></div>
  <div class="abs copyright">© Northvale Design 2023, All Rights Reserved</div>
</footer>

</body>
</html>
```